Fun, Clean Business Card For Family Focused Travel Agency

I need a business card using specific colors and fonts as in the uploaded files. Ideally, I would like a large image of the logo on the back and all the contact info on the front. Maybe the stars/dots somewhere in a flowy form.

I do want it the contact information to be clear and easy to read. I don't want it to look too busy. Maybe even a bit minimalist.

I plan or ordering the ROUNDED CORNER business cards from Cardwell Press, so please consider that in your design.

Target Market(s)

Families with children, couples, groups of friends

Contact Information for Business Card

Marla Quint, Owner
Marla@TumbleTrips.example
Cell Phone Number 555-218-4603
Office Phone Number 555-647-1925
Specializing in Glimmerland destinations, Pelican Bay Fun Park, Cruises and All-Inclusive Vacations.

Nice but not required:
www.TumbleTrips.example
Facebook, Instagram, Twitter icons with username: TumbleTrips

Font styles to use
Sans Serif

Requirements
Must have
• Please try to use the colors from the logo as much as possible. I understand lighter shades/colors may be needed for some things.
Should not have
• NO SERIF FONTS. That is really the only thing I do not want at all

```html
<!DOCTYPE html>
<html lang="en">
<head>
<meta charset="utf-8">
<title>TumbleTrips – Business Card</title>
<link href="https://fonts.googleapis.com/css2?family=Open+Sans:wght@400;600;700&display=swap" rel="stylesheet">
<style>
  :root {
    --page: #e9eaec;
    --card: #222628;
    --card-edge: #2b3033;
    --white: #ffffff;
    --silver: #a9adb0;
    --muted: #c9cccf;
    --teal: #12b39a;
    --teal-dark: #0e8f7b;
  }
  * { box-sizing: border-box; margin: 0; padding: 0; }
  html, body {
    width: 1200px; height: 800px; overflow: hidden;
    background: var(--page);
    font-family: "Open Sans", Arial, sans-serif;
  }
  .sheet {
    width: 1200px; height: 800px;
    display: flex; flex-direction: column; align-items: center; justify-content: center;
    gap: 40px;
  }
  .card {
    position: relative;
    width: 595px; height: 340px;
    background: var(--card);
    border-radius: 18px;
    overflow: hidden;
    box-shadow: 0 10px 30px rgba(0,0,0,.25);
  }

  /* Back */
  .card-back .brand {
    position: absolute; left: 150px; top: 96px;
    display: flex; align-items: center; gap: 18px;
  }
  .brand-dot {
    width: 70px; height: 70px; border-radius: 50%;
    background: #3a3f42;
  }
  .card-back .brand-name {
    font-size: 46px; font-weight: 700; color: var(--silver); letter-spacing: .5px;
  }
  .tagline {
    position: absolute; left: 0; right: 0; top: 206px;
    text-align: center; color: var(--muted); font-size: 14px; line-height: 1.6;
  }
  .tagline strong { font-weight: 700; color: var(--white); }

  /* Front */
  .faint-mark {
    position: absolute; right: -60px; top: -40px;
    width: 300px; height: 300px; border-radius: 50%;
    background: var(--card-edge);
  }
  .card-front .brand {
    position: absolute; left: 60px; top: 44px;
    display: flex; align-items: center; gap: 16px;
  }
  .card-front .brand-dot { width: 62px; height: 62px; background: var(--teal); }
  .card-front .brand-name {
    font-size: 42px; font-weight: 700; color: var(--white);
  }
  .person { position: absolute; left: 60px; top: 160px; }
  .person-name { font-size: 24px; font-weight: 600; color: var(--white); line-height: 1.1; }
  .person-role { font-size: 16px; color: var(--teal); }
  .rule {
    position: absolute; left: 60px; right: 40px; top: 218px;
    height: 1px; background: var(--teal);
  }
  .contacts {
    position: absolute; left: 60px; top: 230px;
    list-style: none; color: var(--white); font-size: 14px;
  }
  .contacts li { display: flex; align-items: center; gap: 8px; height: 22px; }
  .contacts svg { width: 16px; height: 16px; flex: none; }
  .website {
    position: absolute; right: 40px; top: 270px;
    font-size: 13px; font-weight: 600; color: var(--white);
  }
  .website span { color: var(--teal); }
  .band {
    position: absolute; left: 0; right: 0; bottom: 0; height: 14px;
    background: var(--teal);
  }
</style>
</head>
<body>
<main class="sheet">

  <section class="card card-back" aria-label="Card back">
    <div class="brand">
      <span class="brand-dot"></span>
      <span class="brand-name">TumbleTrips</span>
    </div>
    <p class="tagline">
      <strong>Specializing in</strong> Glimmerland destinations<br>
      Pelican Bay Fun Park | Cruises and All-Inclusive Vacations.
    </p>
  </section>

  <section class="card card-front" aria-label="Card front">
    <div class="faint-mark"></div>
    <div class="brand">
      <span class="brand-dot"></span>
      <span class="brand-name">TumbleTrips</span>
    </div>
    <div class="person">
      <p class="person-name">Marla Quint</p>
      <p class="person-role">Owner</p>
    </div>
    <div class="rule"></div>
    <ul class="contacts">
      <li>
        <svg viewBox="0 0 16 16"><circle cx="8" cy="8" r="8" fill="#12b39a"/><rect x="5.5" y="3.5" width="5" height="9" rx="1" fill="#222628"/></svg>
        555-218-4603
      </li>
      <li>
        <svg viewBox="0 0 16 16"><circle cx="8" cy="8" r="8" fill="#12b39a"/><path d="M4 7c0-2 8-2 8 0v1.5H10V7.5H6v1H4z" fill="#222628"/><rect x="5" y="9" width="6" height="3" rx=".5" fill="#222628"/></svg>
        555-647-1925
      </li>
      <li>
        <svg viewBox="0 0 16 16"><circle cx="8" cy="8" r="8" fill="#12b39a"/><rect x="4" y="5" width="8" height="6" rx=".5" fill="#222628"/><path d="M4.3 5.3 8 8.3l3.7-3" stroke="#12b39a" stroke-width="1" fill="none"/></svg>
        Marla@TumbleTrips.example
      </li>
    </ul>
    <p class="website">www.<span>TumbleTrips</span>.example</p>
    <div class="band"></div>
  </section>

</main>
</body>
</html>
```